Otter Bites Guild - A Monthly Subscription Dog Treats Club - Shopify Website Design

A monthly subscription company. Need a Shopify Website Design and uploaded to fully work with Crisp Renewals.

Please look at these sites for examples as well as the images I enclosed.

https://www.mealbrightly.com/
https://www.globalmunchbox.com/

Number of Pages Required

1 page

```html
<!DOCTYPE html>
<html lang="en">
<head>
<meta charset="utf-8">
<title>Otter Bites Guild</title>
<link href="https://fonts.googleapis.com/css2?family=Rajdhani:wght@500;600;700&family=Mulish:wght@300;400;600&display=swap" rel="stylesheet">
<style>
:root{
  --red:#e44d2e;
  --green:#1a9a80;
  --ink:#222;
  --muted:#8a8a8a;
  --band:#f0f1f0;
  --line:#d8d8d8;
  --dark:#1e1e1e;
}
*{box-sizing:border-box;margin:0;padding:0}
html,body{width:1200px;height:5204px;overflow:hidden}
body{position:relative;background:#fff;font-family:'Mulish',sans-serif;color:var(--ink)}
.abs{position:absolute}
.head{font-family:'Rajdhani',sans-serif;font-weight:600;letter-spacing:1px}
.center{text-align:center}
/* top bar */
.promo-bar{left:0;top:0;width:1200px;height:52px;background:var(--red);color:#fff;font-size:14px;display:flex;align-items:center;justify-content:center}
.promo-bar .arrow{position:absolute;top:16px}
/* header */
.pill{height:34px;border-radius:17px;color:#fff;font-size:12px;display:flex;align-items:center;justify-content:center;gap:5px}
.logo-name{font-family:'Rajdhani',sans-serif;font-weight:600;font-size:15px;letter-spacing:1px;color:var(--ink)}
.nav-band{left:0;top:192px;width:1200px;height:68px;background:var(--band)}
.nav-item{top:216px;font-family:'Rajdhani',sans-serif;font-weight:500;font-size:17px;letter-spacing:1px;transform:translateX(-50%)}
.nav-home{left:210px;top:209px;width:92px;height:34px;border:1.5px solid var(--red);border-radius:17px;color:var(--red);font-family:'Rajdhani',sans-serif;font-weight:500;font-size:17px;display:flex;align-items:center;justify-content:center}
/* photo placeholders */
.photo{position:absolute}
.btn-outline{display:flex;align-items:center;justify-content:center;border-radius:26px;font-family:'Rajdhani',sans-serif;font-weight:500;font-size:16px}
/* cards */
.card{position:absolute;border:1px solid #bbb;background:#fff}
.card-shadow{position:absolute;background:#fff;box-shadow:0 0 8px rgba(0,0,0,.12)}
.prod-title{font-family:'Rajdhani',sans-serif;font-weight:600;font-size:13px;letter-spacing:.3px}
.stars{color:var(--ink);font-size:12px;letter-spacing:-1px}
.reviews{font-size:11px;color:#555}
.circle-arrow{width:38px;height:38px;border:1.5px solid var(--red);border-radius:50%;display:flex;align-items:center;justify-content:center}
.section-title{font-family:'Rajdhani',sans-serif;font-weight:600;font-size:46px;letter-spacing:2px;text-align:center;width:1200px;left:0}
.feature-label{font-family:'Rajdhani',sans-serif;font-weight:500;font-size:16px;letter-spacing:.5px;text-align:center;width:200px;line-height:30px}
.para{font-size:14px;color:var(--muted);line-height:31px;font-weight:300}
.read-more{color:var(--red);font-family:'Rajdhani',sans-serif;font-weight:600;font-size:17px;text-decoration:underline}
.footer-nav{top:4932px;font-family:'Rajdhani',sans-serif;font-weight:500;font-size:17px;letter-spacing:.5px;transform:translateX(-50%)}
.social{width:36px;height:36px;border:2px solid var(--ink);border-radius:50%}
.pay{width:46px;height:30px;border-radius:5px}
</style>
</head>
<body>

<!-- top promo bar -->
<div class="abs promo-bar">SAVE UPTO 40% OFF - Nemo enim ipsam voluptatem quia voluptas sit
  <svg class="arrow" style="left:96px" width="12" height="20" viewBox="0 0 12 20"><path d="M10 2 2 10l8 8" fill="none" stroke="#fff" stroke-width="2.5"/></svg>
  <svg class="arrow" style="left:1086px" width="12" height="20" viewBox="0 0 12 20"><path d="M2 2l8 8-8 8" fill="none" stroke="#fff" stroke-width="2.5"/></svg>
</div>

<!-- header -->
<div class="abs pill" style="left:110px;top:96px;width:122px;background:var(--green)">ENGLISH ▾</div>
<div class="abs pill" style="left:239px;top:96px;width:122px;background:var(--red)">USD $ ▾</div>
<div class="abs center" style="left:500px;top:110px;width:200px">
  <svg width="20" height="20" viewBox="0 0 20 20" style="vertical-align:middle"><circle cx="10" cy="10" r="8" fill="none" stroke="var(--ink)" stroke-width="1.5"/></svg>
  <span class="logo-name" style="vertical-align:middle">OTTER BITES GUILD</span>
</div>
<svg class="abs" style="left:980px;top:104px" width="110" height="24" viewBox="0 0 110 24">
  <circle cx="20" cy="11" r="7" fill="none" stroke="#222" stroke-width="2"/><path d="M25 16l5 5" stroke="#222" stroke-width="2"/>
  <circle cx="59" cy="7" r="5" fill="none" stroke="#222" stroke-width="2"/><path d="M50 21c0-6 4-8 9-8s9 2 9 8z" fill="none" stroke="#222" stroke-width="2"/>
  <path d="M88 4h4l3 12h11l2-8H93" fill="none" stroke="#222" stroke-width="2"/><circle cx="96" cy="20" r="1.8" fill="#222"/><circle cx="105" cy="20" r="1.8" fill="#222"/>
</svg>

<!-- navigation -->
<div class="abs nav-band"></div>
<div class="abs nav-home">HOME</div>
<div class="abs nav-item" style="left:367px">ABOUT</div>
<div class="abs nav-item" style="left:478px">SHOP</div>
<div class="abs nav-item" style="left:604px">PRODUCTS</div>
<div class="abs nav-item" style="left:735px">BLOGS</div>
<div class="abs nav-item" style="left:841px">FAQ</div>
<div class="abs nav-item" style="left:955px">CONTACT</div>

<!-- hero -->
<div class="photo" role="img" aria-label="Dog sitting on grass taking a treat from its owner's hand" style="left:0;top:260px;width:1200px;height:558px;background:linear-gradient(110deg,#6d6a4a 0%,#3f4a2f 40%,#2d3026 70%,#4a5560 100%)"></div>
<div class="abs head center" style="left:0;top:418px;width:1200px;font-size:78px;color:#fff;letter-spacing:3px">OTTER BITES GUILD</div>
<div class="abs center" style="left:0;top:516px;width:1200px;font-size:15px;color:#fff;line-height:31px">Nemo enim ipsam voluptatem quia voluptas sit aspernatur aut odit aut fugit,<br>sed quia consequuntur magni dolores eos</div>
<div class="abs btn-outline" style="left:507px;top:592px;width:155px;height:48px;border:1.5px solid #fff;color:#fff">SHOP NOW</div>
<div class="abs" style="left:525px;top:791px;width:38px;height:4px;background:#fff"></div>
<div class="abs" style="left:581px;top:791px;width:38px;height:4px;background:var(--red)"></div>
<div class="abs" style="left:637px;top:791px;width:38px;height:4px;background:#fff"></div>

<!-- promo grid -->
<div class="photo" role="img" aria-label="Woman sitting on the floor giving a treat to a small dog" style="left:48px;top:920px;width:472px;height:558px;background:linear-gradient(135deg,#8e877e,#4d4a47 60%,#2f3336)"></div>
<div class="abs head center" style="left:48px;top:1136px;width:472px;font-size:19px;color:#fff">LOREM IPSUM DOLOR SIT AMET, CONSECTETUR</div>
<div class="abs center" style="left:48px;top:1170px;width:472px;font-size:12px;color:#eee">Nemo enim ipsam voluptatem quia voluptas</div>
<div class="abs btn-outline" style="left:206px;top:1210px;width:156px;height:48px;border:1.5px solid #fff;color:#fff">SHOP NOW</div>
<div class="card-shadow" style="left:540px;top:920px;width:298px;height:266px"><div role="img" aria-label="Treat bags in an open shipping box" style="margin:40px auto;width:190px;height:186px;background:radial-gradient(circle,#c99a6a,#e8d9c4 65%,#fff 70%)"></div></div>
<div class="card-shadow" style="left:855px;top:920px;width:298px;height:266px"><div role="img" aria-label="Sausage chews in a box" style="margin:40px auto;width:200px;height:186px;background:radial-gradient(circle,#d9573a,#e4c7ae 65%,#fff 70%)"></div></div>
<div class="card-shadow" style="left:540px;top:1208px;width:298px;height:268px"><div role="img" aria-label="Puppy sniffing a box of chews" style="margin:40px auto;width:200px;height:188px;background:radial-gradient(circle,#9a8a78,#e7ddd1 65%,#fff 70%)"></div></div>
<div class="abs" style="left:855px;top:1208px;width:298px;height:268px;background:var(--red);box-shadow:0 0 8px rgba(0,0,0,.12)"></div>
<div class="abs head center" style="left:855px;top:1310px;width:298px;font-size:21px;color:#fff;line-height:32px;letter-spacing:.5px">FREE SHIPPING ON OREDERS<br>$100.00</div>

<!-- our products -->
<div class="abs section-title" style="top:1570px">OUR PRODUCTS</div>
<div class="abs circle-arrow" style="left:1047px;top:1582px"><svg width="10" height="14" viewBox="0 0 10 14"><path d="M2 1l6 6-6 6" fill="none" stroke="var(--red)" stroke-width="2"/></svg></div>
<div class="photo" role="img" aria-label="Woman in a field feeding a golden retriever" style="left:107px;top:1648px;width:490px;height:368px;background:linear-gradient(120deg,#d9a556,#9a8b45 45%,#5b6a2c)"></div>
<div class="card" style="left:606px;top:1648px;width:237px;height:270px"><div role="img" aria-label="Bone shaped biscuits in a gift box" style="margin:50px auto;width:170px;height:170px;background:radial-gradient(circle,#c79a67,#efe3d4 60%,#fff 70%)"></div></div>
<div class="card" style="left:853px;top:1648px;width:237px;height:270px"><div role="img" aria-label="Dried meat chews in a box" style="margin:50px auto;width:170px;height:170px;background:radial-gradient(circle,#6a3a24,#e3cbb6 60%,#fff 70%)"></div></div>
<div class="abs prod-title" style="left:608px;top:1934px">LOREM IPSUM DOLOR SIT AMET</div>
<div class="abs" style="left:608px;top:1960px"><span class="stars" style="color:var(--red)">★★★★★</span> <span class="reviews">125(Reviews)</span></div>
<div class="abs head" style="left:613px;top:1988px;font-size:17px">$212.00</div>
<div class="abs prod-title" style="left:855px;top:1934px">LOREM IPSUM DOLOR SIT AMET</div>
<div class="abs" style="left:855px;top:1960px"><span class="stars" style="color:var(--red)">★★★★★</span> <span class="reviews">125(Reviews)</span></div>
<div class="abs head" style="left:860px;top:1988px;font-size:17px">$212.00</div>

<!-- featured products -->
<div class="abs" style="left:0;top:2116px;width:1200px;height:510px;background:var(--band)"></div>
<div class="abs section-title" style="top:2162px">FEATURED PRODUCTS</div>

<div class="card" style="left:110px;top:2252px;width:238px;height:318px"><div role="img" aria-label="Bulldog puppy in a cardboard box" style="margin:18px auto;width:180px;height:180px;background:radial-gradient(circle,#b18a66,#ede2d6 60%,#fff 70%)"></div></div>
<div class="abs center" style="left:126px;top:2266px;width:48px;height:48px;border-radius:50%;background:var(--green);color:#fff;font-size:11px;line-height:14px;padding-top:10px">10%<br>Off</div>
<div class="abs prod-title" style="left:122px;top:2486px">LOREM IPSUM DOLOR SIT</div>
<div class="abs" style="left:122px;top:2510px"><span class="stars">★★★★★</span> <span class="reviews">140Reviews</span></div>
<div class="abs" style="left:122px;top:2536px;font-size:12px;font-weight:600"><span style="color:var(--red)">$100.00</span> &nbsp;<s style="color:#888">$100.00</s></div>

<div class="card" style="left:357px;top:2252px;width:238px;height:318px"><div role="img" aria-label="Colourful bone biscuits in a black box" style="margin:18px auto;width:180px;height:180px;background:radial-gradient(circle,#6b8a4c,#e9e3dc 60%,#fff 70%)"></div></div>
<div class="abs prod-title" style="left:369px;top:2486px">LOREM IPSUM DOLOR SIT</div>
<div class="abs" style="left:369px;top:2510px"><span class="stars">★★★★★</span> <span class="reviews">140Reviews</span></div>
<div class="abs" style="left:369px;top:2536px;font-size:12px;font-weight:600;color:var(--red)">$100.00</div>

<div class="card" style="left:604px;top:2252px;width:238px;height:318px"><div role="img" aria-label="Assorted chews in an open box" style="margin:18px auto;width:180px;height:180px;background:radial-gradient(circle,#8a6a55,#e6e3e0 60%,#fff 70%)"></div></div>
<div class="abs prod-title" style="left:616px;top:2486px">LOREM IPSUM DOLOR SIT</div>
<div class="abs" style="left:616px;top:2510px"><span class="stars">★★★★★</span> <span class="reviews">140Reviews</span></div>
<div class="abs" style="left:616px;top:2536px;font-size:12px;font-weight:600;color:var(--red)">$100.00</div>

<div class="card" style="left:851px;top:2252px;width:238px;height:318px"><div role="img" aria-label="Dried meat chews in a box" style="margin:18px auto;width:180px;height:180px;background:radial-gradient(circle,#6a3a24,#e3cbb6 60%,#fff 70%)"></div></div>
<div class="abs prod-title" style="left:863px;top:2486px">LOREM IPSUM DOLOR SIT</div>
<div class="abs" style="left:863px;top:2510px"><span class="stars">★★★★★</span> <span class="reviews">140Reviews</span></div>
<div class="abs" style="left:863px;top:2536px;font-size:12px;font-weight:600;color:var(--red)">$100.00</div>

<div class="abs circle-arrow" style="left:1095px;top:2409px"><svg width="10" height="14" viewBox="0 0 10 14"><path d="M2 1l6 6-6 6" fill="none" stroke="var(--red)" stroke-width="2"/></svg></div>

<!-- about -->
<div class="card-shadow" style="left:110px;top:2730px;width:495px;height:428px"><div role="img" aria-label="Beagle puppy eating from a metal bowl" style="margin:60px auto;width:440px;height:300px;background:radial-gradient(ellipse,#6b4a32,#cdbcad 55%,#fff 72%)"></div></div>
<div class="abs head" style="left:623px;top:2792px;font-size:46px;letter-spacing:2px">ABOUT US</div>
<div class="abs para" style="left:623px;top:2860px;width:455px">Nemo enim ipsam voluptatem quia voluptas sit aspernatur aut odit aut fugit, sed quia consequuntur magni dolores eos qui ratione voluptatem sequi nesciunt. Neque porro quisquam est, qui dolorem ipsum quia dolor sit amet, consectetur, adipisci velit, sed quia non numquam eius modi</div>
<div class="abs btn-outline" style="left:623px;top:3036px;width:155px;height:52px;border:1.5px solid var(--red);color:var(--red)">READ MORE</div>

<!-- features -->
<div class="abs" style="left:0;top:3262px;width:1200px;height:250px;background:var(--band)"></div>
<svg class="abs" style="left:0;top:3300px" width="1200" height="110" viewBox="0 0 1200 110">
  <g fill="none" stroke="var(--red)" stroke-width="2">
    <circle cx="183" cy="52" r="47"/><path d="M170 75c0-25 10-38 30-44-2 22-10 36-30 44zM170 75l14-26"/>
    <circle cx="391" cy="52" r="47"/><rect x="370" y="35" width="26" height="20" rx="3"/><path d="M376 42h14M376 48h10"/><circle cx="404" cy="58" r="8"/><path d="M372 62l10 10"/>
    <circle cx="600" cy="52" r="47"/><path d="M590 38h20l-4-8h-12zM585 75c0-20 10-34 15-37 5 3 15 17 15 37z"/><path d="M596 52c6-2 8 4 4 6s-4 8 3 6M600 48v22"/>
    <circle cx="807" cy="52" r="47"/><rect x="783" y="36" width="30" height="24"/><path d="M813 44h10l6 8v8h-16"/><circle cx="792" cy="64" r="4"/><circle cx="822" cy="64" r="4"/>
    <circle cx="1015" cy="52" r="47"/><circle cx="1015" cy="46" r="15"/><circle cx="1015" cy="46" r="9"/><path d="M1006 58l-5 20 8-4 4 7 2-16M1024 58l5 20-8-4-4 7"/>
  </g>
</svg>
<div class="abs feature-label" style="left:83px;top:3414px">90% FEWER CARBS</div>
<div class="abs feature-label" style="left:291px;top:3414px">MORE ANIMAL<br>PROTEIN</div>
<div class="abs feature-label" style="left:500px;top:3414px">30 DAY MONEY-BACK<br>GUARANTEE</div>
<div class="abs feature-label" style="left:707px;top:3414px">FREE SHIPPING</div>
<div class="abs feature-label" style="left:915px;top:3414px">AWARD WINNER</div>

<!-- latest news -->
<div class="abs section-title" style="top:3602px">LATEST NEWS</div>
<div class="photo" role="img" aria-label="Pile of colourful bone shaped biscuits" style="left:110px;top:3674px;width:482px;height:428px;background:linear-gradient(135deg,#7a4a4e,#a98a6a 50%,#5a3a3c)"></div>
<div class="photo" role="img" aria-label="Shepherd mix dog sitting on a concrete floor" style="left:607px;top:3674px;width:482px;height:428px;background:linear-gradient(180deg,#9c9c9a,#8a7f70 55%,#a3a3a1)"></div>
<div class="abs prod-title" style="left:110px;top:4124px">LOREM IPSUM DOLOR SIT AMET, CONSECTETUR ADIPISCING ELIT</div>
<div class="abs" style="left:110px;top:4154px;font-size:14px">Posted by - samreyes &nbsp;&nbsp;&nbsp; September 25-2020</div>
<div class="abs para" style="left:110px;top:4182px;width:482px;font-size:14px">Nemo enim ipsam voluptatem quia voluptas sit aspernatur aut odit aut fugit, sed quia consequuntur</div>
<div class="abs read-more" style="left:110px;top:4258px">READ MORE</div>
<div class="abs prod-title" style="left:607px;top:4124px">LOREM IPSUM DOLOR SIT AMET, CONSECTETUR ADIPISCING ELIT</div>
<div class="abs" style="left:607px;top:4154px;font-size:14px">Posted by - samreyes &nbsp;&nbsp;&nbsp; September 25-2020</div>
<div class="abs para" style="left:607px;top:4182px;width:482px;font-size:14px">Nemo enim ipsam voluptatem quia voluptas sit aspernatur aut odit aut fugit, sed quia consequuntur</div>
<div class="abs read-more" style="left:607px;top:4258px">READ MORE</div>

<!-- newsletter -->
<div class="photo" role="img" aria-label="Close-up of a red-haired dog" style="left:0;top:4384px;width:1200px;height:436px;background:linear-gradient(120deg,#5a3a2a,#8c5a3c 40%,#4a3a32 75%,#6a6a66)"></div>
<div class="abs" style="left:265px;top:4464px;width:670px;height:274px;background:rgba(255,255,255,.93)"></div>
<div class="abs head center" style="left:265px;top:4490px;width:670px;font-size:44px;letter-spacing:2px">NEWSLETTER SIGNUP</div>
<div class="abs center" style="left:265px;top:4554px;width:670px;font-size:14px;color:#555">Nemo enim ipsam voluptatem quia voluptas sit</div>
<div class="abs" style="left:338px;top:4596px;width:522px;height:48px;border:1px solid #ccc;background:#fff"></div>
<div class="abs" style="left:352px;top:4611px;font-size:14px;color:#888">Your Email</div>
<div class="abs head" style="left:709px;top:4596px;width:151px;height:48px;background:var(--red);color:#fff;font-size:15px;display:flex;align-items:center;justify-content:center">SUBSCRIBE</div>
<div class="abs head center" style="left:265px;top:4668px;width:670px;font-size:22px"><span style="color:var(--red)">GET 20%OFF</span> &nbsp;FIRST ORDER</div>

<!-- footer -->
<div class="abs" style="left:110px;top:4900px;width:150px">
  <svg width="24" height="24" viewBox="0 0 24 24" style="vertical-align:middle"><circle cx="12" cy="12" r="10" fill="none" stroke="var(--ink)" stroke-width="1.5"/></svg>
  <span class="logo-name" style="font-size:15px;vertical-align:middle">OTTER BITES<br>GUILD</span>
</div>
<div class="abs footer-nav" style="left:350px">HOME</div>
<div class="abs footer-nav" style="left:463px">ABOUT</div>
<div class="abs footer-nav" style="left:574px">SHOP</div>
<div class="abs footer-nav" style="left:700px">PRODUCTS</div>
<div class="abs footer-nav" style="left:831px">BLOGS</div>
<div class="abs footer-nav" style="left:936px">FAQ</div>
<div class="abs footer-nav" style="left:1050px">CONTACT</div>
<div class="abs head" style="left:110px;top:5018px;font-size:17px;font-weight:500">FOLLOW US</div>
<div class="abs social" style="left:110px;top:5057px"></div>
<div class="abs social" style="left:166px;top:5057px"></div>
<div class="abs social" style="left:222px;top:5057px"></div>

<!-- bottom bar -->
<div class="abs" style="left:0;top:5116px;width:1200px;height:88px;background:var(--dark)"></div>
<div class="abs" style="left:110px;top:5151px;font-size:14px;color:#ddd">© 2020 All Rights Reserved</div>
<div class="abs pay" style="left:494px;top:5145px;background:#3a4a7a"></div>
<div class="abs pay" style="left:560px;top:5145px;background:#c6442b"></div>
<div class="abs pay" style="left:618px;top:5145px;background:#2c5aa0"></div>
<div class="abs pay" style="left:676px;top:5145px;width:30px;background:#4a8ac6"></div>
<div class="abs" style="left:955px;top:5151px;font-size:14px;color:#ddd">Terms &amp; Conditions</div>

</body>
</html>
```